Thornbury Building Company - Card Design

I am looking to use the logo designs that you already did for me to develop a business card. I would like the card to have a black background and be double sided. I want white and green logo and text. I have attached an inspiration photo of a look that I like. I would like to use the Vertical Logo attached to take up the full front side of the card. On the back where I have my name and information, I would like to have the horizontal logo or maybe even just the image of the 'A' and trees without the text. I am open, but I am looking for something clean and simple and I want the green to really pop! Additional files can be found under Design #: 58302946

Target Market(s)

Homeowners

Industry/Entity Type

Construction

Contact Information for Business Card

Name: Marcus Thornbury, Title: Project Manager, Phone: 555.274.8136, Email: thornburybuildingcompany@mailvesta.com, address: 487 Larkspur Ln, Felton, CA 95033, Lic# 2468317

Colors
00AB8E
00BBA5
67D7C9
C6EFE9
E9F9F6

Requirements
Nice to have
• I would like to see the logos that I have already got from ArtLoomHub, though I am open to new ones

```html
<!DOCTYPE html>
<html lang="en">
<head>
<meta charset="utf-8">
<title>Thornbury Building Company – Business Card</title>
<link href="https://fonts.googleapis.com/css2?family=Lato:wght@400;700;900&family=Michroma&display=swap" rel="stylesheet">
<style>
  :root {
    --backdrop: #1c1c1c;
    --card-black: #231f20;
    --green: #6cb545;
    --white: #ffffff;
    --soft-white: #e8e8e8;
  }
  * { box-sizing: border-box; margin: 0; padding: 0; }
  html, body { width: 1200px; height: 900px; overflow: hidden; }
  body {
    background: var(--backdrop);
    font-family: "Lato", sans-serif;
    position: relative;
  }
  .card {
    position: absolute;
    background: var(--card-black);
    border-radius: 22px;
    overflow: hidden;
    box-shadow: 0 12px 30px rgba(0,0,0,.45);
  }

  /* Front */
  .card-front { left: 75px; top: 270px; width: 630px; height: 360px; }
  .front-est {
    position: absolute;
    font-family: "Michroma", sans-serif;
    color: var(--white);
    font-size: 15px;
    letter-spacing: 6px;
    padding: 6px 0;
    border-top: 1.5px solid var(--green);
    border-bottom: 1.5px solid var(--green);
  }
  .front-est.label { left: 58px; top: 82px; }
  .front-est.year { right: 58px; top: 236px; }
  .wordmark {
    position: absolute;
    left: 0; right: 0; top: 128px;
    display: flex; align-items: center; justify-content: center; gap: 16px;
  }
  .wordmark-square { width: 22px; height: 22px; background: var(--green); }
  .wordmark-name {
    font-family: "Lato", sans-serif;
    font-weight: 900;
    color: var(--white);
    font-size: 40px;
    line-height: 1.05;
    letter-spacing: 2px;
    text-transform: uppercase;
  }

  /* Back */
  .card-back { left: 765px; top: 135px; width: 360px; height: 630px; }
  .back-panel { position: absolute; left: 0; top: 0; }
  .contact {
    position: absolute;
    left: 0; right: 0; top: 318px;
    text-align: center;
    color: var(--white);
  }
  .contact-name {
    font-weight: 900;
    font-size: 29px;
    letter-spacing: .5px;
    text-transform: uppercase;
  }
  .contact-title {
    color: var(--green);
    font-size: 17px;
    margin-top: 4px;
  }
  .rule { width: 250px; height: 2px; background: var(--green); margin: 18px auto; }
  .icon-row { display: flex; justify-content: center; gap: 12px; margin-bottom: 14px; }
  .icon {
    width: 28px; height: 28px; border-radius: 50%;
    background: var(--green);
    display: flex; align-items: center; justify-content: center;
  }
  .contact-lines { font-size: 15px; line-height: 1.55; color: var(--soft-white); }
  .contact-lines .phone { font-size: 18px; }
  .license { font-size: 15px; color: var(--soft-white); }
</style>
</head>
<body>

  <section class="card card-front" aria-label="Card front">
    <div class="front-est label">ESTD</div>
    <div class="wordmark">
      <span class="wordmark-square"></span>
      <span class="wordmark-name">Thornbury<br>Building Company</span>
    </div>
    <div class="front-est year">2020</div>
  </section>

  <section class="card card-back" aria-label="Card back">
    <svg class="back-panel" width="360" height="630" viewBox="0 0 360 630">
      <polygon points="0,0 360,0 360,40 0,300" fill="var(--green)"/>
    </svg>
    <div class="contact">
      <div class="contact-name">Marcus Thornbury</div>
      <div class="contact-title">Project Manager</div>
      <div class="rule"></div>
      <div class="icon-row">
        <span class="icon">
          <svg width="14" height="14" viewBox="0 0 24 24"><path d="M6.6 10.8a15 15 0 0 0 6.6 6.6l2.2-2.2a1 1 0 0 1 1-.25 11.4 11.4 0 0 0 3.6.57 1 1 0 0 1 1 1V20a1 1 0 0 1-1 1A17 17 0 0 1 3 4a1 1 0 0 1 1-1h3.5a1 1 0 0 1 1 1c0 1.25.2 2.45.57 3.57a1 1 0 0 1-.25 1z" fill="var(--card-black)"/></svg>
        </span>
        <span class="icon">
          <svg width="14" height="14" viewBox="0 0 24 24"><rect x="3" y="5" width="18" height="14" rx="1.5" fill="var(--card-black)"/><path d="M3.5 6l8.5 7 8.5-7" stroke="var(--green)" stroke-width="1.8" fill="none"/></svg>
        </span>
        <span class="icon">
          <svg width="14" height="14" viewBox="0 0 24 24"><path d="M12 2a7 7 0 0 0-7 7c0 5 7 13 7 13s7-8 7-13a7 7 0 0 0-7-7zm0 9.5A2.5 2.5 0 1 1 12 6.5a2.5 2.5 0 0 1 0 5z" fill="var(--card-black)"/></svg>
        </span>
      </div>
      <div class="contact-lines">
        <div class="phone">555.274.8136</div>
        <div>thornburybuildingcompany@mailvesta.com</div>
        <div>487 Larkspur Ln, Felton, CA 95033</div>
      </div>
      <div class="rule"></div>
      <div class="license">Lic# 2468317</div>
    </div>
  </section>

</body>
</html>
```